Limbwell Nine tri-fold brochure

Create a three panel brochure, front and back, for company named Limbwell Nine. It should have a modern and high-tech feel. It should appeal to not only patients but also physicians, physical therapists, and other medical personnel. Stock photos are fine but our logo must be included. You can also use the pictures from our website which is stridevek.example or limbwell9.example. They are the same website but we are rebranding for stridevek orthotics to limbwell nine. Should also state "Hablamos Espanol" on the front of the brochure somewhere.
Updates

Target Market(s)

Amputees, Physicians, and Therapists

Industry/Entity Type

It Company

Requirements
Must have
• Limbwell Nine logo
• Office Locations:
• 4827 Quillby Road, Ste 305
• Memphis, TN 38119
• Phone (901) 555-0142
• Fax (901) 555-0187
• 20947 Brackenfold Way, Ste C
• Houston, TX 77082
• Phone: (281) 555-0163
• Fax: (281)555-0119
• 7460 Venturi Street, Ste 400
• Arlington, TX 76015
• Phone: (682) 555-0134
• Fax: (682) 555-0178
• Hablamos EspaƱol
Nice to have
• Emphasis on patient care

```html
<!DOCTYPE html>
<html lang="en">
<head>
<meta charset="utf-8">
<title>Limbwell Nine tri-fold brochure</title>
<link href="https://fonts.googleapis.com/css2?family=Open+Sans:wght@400;600;700&display=swap" rel="stylesheet">
<style>
:root{
  --blue:#1580dc;
  --blue-deep:#0c62c6;
  --navy:#15237a;
  --navy-deep:#0d1657;
  --red:#d3121d;
  --ink:#2b2b2b;
  --link-blue:#1d3f9a;
  --page:#e4e4e4;
}
*{box-sizing:border-box;margin:0;padding:0}
html,body{width:880px;height:1200px;overflow:hidden}
body{background:var(--page);font-family:"Open Sans",Arial,sans-serif;position:relative}
.sheet{position:absolute;left:89px;width:702px;height:496px;background:#fff;overflow:hidden;box-shadow:0 6px 14px rgba(0,0,0,.28)}
.sheet--outer{top:86px}
.sheet--inner{top:655px}
.panel{position:absolute;top:0;width:234px;height:100%}
.panel--1{left:0}.panel--2{left:234px}.panel--3{left:468px}
.bg-blue{background:linear-gradient(160deg,var(--blue) 0%,var(--blue-deep) 100%)}
.bg-navy{background:linear-gradient(180deg,var(--navy) 0%,var(--navy-deep) 100%)}
.fold{position:absolute;top:0;width:1px;height:100%;background:rgba(0,0,0,.06)}
.photo{position:absolute}
.swoosh{position:absolute;left:0;top:0;width:702px;height:496px}
.content{position:absolute;color:#fff}
h2.panel-title{font-size:16px;font-weight:700;margin-bottom:12px}
.mission p{font-size:8.4px;line-height:1.42;margin-bottom:8px;text-align:justify}
.locations{left:234px;width:234px;top:20px;text-align:center}
.locations .pill{display:inline-block;border:1px solid rgba(255,255,255,.7);border-radius:12px;padding:2px 24px;font-size:12.5px}
.office{font-size:7.3px;line-height:1.7;padding:10px 0 8px;margin:0 28px;border-bottom:1px solid rgba(255,255,255,.12)}
.office:last-child{border-bottom:0}
.office .pin{display:block;margin:0 auto 4px}
.office svg.ico{vertical-align:-1px;margin-right:2px}
.social{left:234px;width:234px;top:453px;display:flex;justify-content:center;gap:8px}
.social span{width:15px;height:15px;border-radius:50%;background:var(--link-blue)}
.web{position:absolute;font-size:11px;color:#1b1b1b;display:flex;align-items:center;gap:5px}
.brand{position:absolute;left:560px;top:412px;display:flex;align-items:center;gap:6px;color:var(--red);font-size:16px;font-weight:600}
.brand i{width:14px;height:14px;border-radius:50%;background:var(--red);display:block}
.spanish{position:absolute;left:580px;top:437px;font-size:10px;font-weight:600;color:var(--navy)}
.services{left:22px;top:24px;width:200px}
.services h2{font-size:17px;margin-bottom:12px}
.svc{display:flex;gap:6px;margin-bottom:11px;font-size:11px;line-height:1.35}
.svc b{font-weight:700;display:block}
.svc svg{flex:none;margin-top:2px}
.includes{left:257px;top:28px;width:190px;color:var(--link-blue)}
.includes h3{color:var(--red);font-size:13.5px;line-height:1.35;font-weight:700;margin-bottom:10px}
.includes p{font-size:8.8px;line-height:1.45}
.benefits{left:491px;top:24px;width:200px;color:var(--ink)}
.benefits h3{color:var(--red);font-size:13.5px;font-weight:400;line-height:1.35;margin-bottom:12px}
.benefits li{list-style:none;display:flex;gap:7px;font-size:9.8px;line-height:1.4;margin-bottom:5px}
.benefits li svg{flex:none;margin-top:2px}
.contact{left:28px;top:439px;color:var(--ink);font-size:11.5px;line-height:1.7}
.contact div{display:flex;align-items:center;gap:6px}
</style>
</head>
<body>

<section class="sheet sheet--outer" aria-label="Brochure outside">
  <div class="panel panel--1 bg-blue"></div>
  <div class="panel panel--2 bg-navy"></div>
  <div class="panel panel--3 photo" role="img" aria-label="Photo of a sprinter with a running blade prosthesis on a track" style="height:394px;background:linear-gradient(180deg,#5f7a4e 0%,#3e6fb0 45%,#2b4f9c 70%,#b59a86 100%)"></div>
  <div class="photo" role="img" aria-label="Illustration of a robotic hand reaching toward a human hand in blue light" style="left:234px;top:290px;width:234px;height:112px;background:radial-gradient(ellipse at 60% 40%,#9fb8f2 0%,#3e56b8 35%,var(--navy-deep) 80%)"></div>

  <svg class="swoosh" viewBox="0 0 702 496" aria-hidden="true">
    <defs><linearGradient id="paperA" x1="0" y1="0" x2="0" y2="1"><stop offset="0" stop-color="#fff"/><stop offset="1" stop-color="#dadada"/></linearGradient></defs>
    <path d="M0,340 C160,395 320,418 470,392 C580,372 650,335 702,300 L702,496 L0,496Z" fill="url(#paperA)"/>
    <path d="M0,348 C160,403 320,426 470,400 C580,380 650,343 702,308" fill="none" stroke="#1f6fd1" stroke-width="6"/>
    <path d="M0,338 C160,393 320,416 470,390 C580,370 650,333 702,298" fill="none" stroke="var(--red)" stroke-width="8"/>
  </svg>

  <div class="photo" role="img" aria-label="Photo of a decorated prosthetic socket and a prosthetic leg with foot" style="left:40px;top:274px;width:160px;height:210px;border-radius:40px 40px 10px 10px;background:linear-gradient(160deg,#3a3a3a 0%,#7a7a7a 50%,#d2553a 100%);opacity:.9"></div>
  <div class="fold" style="left:234px"></div><div class="fold" style="left:468px"></div>

  <div class="content mission" style="left:23px;top:20px;width:188px">
    <h2 class="panel-title">Our Mission</h2>
    <p>To utilize education, experience and dedication in an effort to provide the most comprehensive prosthetic and orthotic care available.</p>
    <p>Our professionals are fully trained to evaluate, fabricate and fit every type of artificial limb and brace for the adult and pediatric population. We offer support and understanding as we counsel our patients in a safe and effective utilization of our devices. No two patients are the same at Limbwell Nine.</p>
    <p>We pride ourselves in treating every patient as an individual with dignity and respect.</p>
    <p>We guarantee high quality and fast turnaround on all our products.</p>
  </div>

  <div class="content locations">
    <span class="pill">Office Locations:</span>
    <div class="office">
      <svg class="pin" width="12" height="12" viewBox="0 0 12 12"><circle cx="6" cy="6" r="5.5" fill="none" stroke="#fff" stroke-width=".7"/><path d="M6 2.8a1.8 1.8 0 0 1 1.8 1.8C7.8 6 6 8.6 6 8.6S4.2 6 4.2 4.6A1.8 1.8 0 0 1 6 2.8z" fill="#fff"/></svg>
      4827 Quillby Road, Ste 305<br>Memphis, TN 38119<br>
      <svg class="ico" width="7" height="7" viewBox="0 0 8 8"><circle cx="4" cy="4" r="3.5" fill="none" stroke="#fff" stroke-width=".8"/><path d="M2.7 2.4l1 1-.5.6.8.8.6-.5 1 1-.6.6c-1.4-.3-2.6-1.5-2.9-2.9z" fill="#fff"/></svg>(901) 555-0142<br>
      <svg class="ico" width="7" height="7" viewBox="0 0 8 8"><rect x="1" y="3" width="6" height="4" fill="#fff"/><rect x="2" y="1" width="4" height="2" fill="#fff"/></svg>(901) 555-0187
    </div>
    <div class="office">
      <svg class="pin" width="12" height="12" viewBox="0 0 12 12"><circle cx="6" cy="6" r="5.5" fill="none" stroke="#fff" stroke-width=".7"/><path d="M6 2.8a1.8 1.8 0 0 1 1.8 1.8C7.8 6 6 8.6 6 8.6S4.2 6 4.2 4.6A1.8 1.8 0 0 1 6 2.8z" fill="#fff"/></svg>
      20947 Brackenfold Way, Ste C<br>Houston, TX 77082<br>
      <svg class="ico" width="7" height="7" viewBox="0 0 8 8"><circle cx="4" cy="4" r="3.5" fill="none" stroke="#fff" stroke-width=".8"/><path d="M2.7 2.4l1 1-.5.6.8.8.6-.5 1 1-.6.6c-1.4-.3-2.6-1.5-2.9-2.9z" fill="#fff"/></svg>(281) 555-0163<br>
      <svg class="ico" width="7" height="7" viewBox="0 0 8 8"><rect x="1" y="3" width="6" height="4" fill="#fff"/><rect x="2" y="1" width="4" height="2" fill="#fff"/></svg>(281)555-0119
    </div>
    <div class="office">
      <svg class="pin" width="12" height="12" viewBox="0 0 12 12"><circle cx="6" cy="6" r="5.5" fill="none" stroke="#fff" stroke-width=".7"/><path d="M6 2.8a1.8 1.8 0 0 1 1.8 1.8C7.8 6 6 8.6 6 8.6S4.2 6 4.2 4.6A1.8 1.8 0 0 1 6 2.8z" fill="#fff"/></svg>
      7460 Venturi Street, Ste 400<br>Arlington, TX 76015<br>
      <svg class="ico" width="7" height="7" viewBox="0 0 8 8"><circle cx="4" cy="4" r="3.5" fill="none" stroke="#fff" stroke-width=".8"/><path d="M2.7 2.4l1 1-.5.6.8.8.6-.5 1 1-.6.6c-1.4-.3-2.6-1.5-2.9-2.9z" fill="#fff"/></svg>(682) 555-0134<br>
      <svg class="ico" width="7" height="7" viewBox="0 0 8 8"><rect x="1" y="3" width="6" height="4" fill="#fff"/><rect x="2" y="1" width="4" height="2" fill="#fff"/></svg>(682) 555-0178
    </div>
  </div>

  <div class="content social" aria-hidden="true"><span></span><span></span><span></span><span></span></div>
  <div class="web" style="left:290px;top:470px"><svg width="10" height="10" viewBox="0 0 10 10"><circle cx="5" cy="5" r="4.3" fill="none" stroke="var(--red)"/><path d="M.7 5h8.6M5 .7c-2.4 2.6-2.4 6 0 8.6M5 .7c2.4 2.6 2.4 6 0 8.6" fill="none" stroke="var(--red)" stroke-width=".7"/></svg>www.limbwell9.example</div>
  <div class="brand"><i></i>Limbwell Nine</div>
  <div class="spanish">Hablamos Español</div>
  <div class="web" style="left:523px;top:470px"><svg width="10" height="10" viewBox="0 0 10 10"><circle cx="5" cy="5" r="4.3" fill="none" stroke="var(--red)"/><path d="M.7 5h8.6M5 .7c-2.4 2.6-2.4 6 0 8.6M5 .7c2.4 2.6 2.4 6 0 8.6" fill="none" stroke="var(--red)" stroke-width=".7"/></svg>www.limbwell9.example</div>
</section>

<section class="sheet sheet--inner" aria-label="Brochure inside">
  <div class="panel panel--1 bg-blue"></div>
  <div class="photo" role="img" aria-label="Photo of a young clinician at a laptop fitting a prosthetic arm for a patient" style="left:234px;top:193px;width:234px;height:256px;background:linear-gradient(180deg,#f2f2f2 0%,#c9b49c 40%,#3d5b86 75%,#2f4b73 100%)"></div>
  <div class="photo" role="img" aria-label="Photo of a smiling patient in a yellow shirt wearing a prosthetic arm" style="left:468px;top:205px;width:234px;height:212px;background:linear-gradient(180deg,#f4f4f4 0%,#e2b48f 45%,#f2c31f 80%,#e5b41a 100%)"></div>

  <svg class="swoosh" viewBox="0 0 702 496" aria-hidden="true">
    <defs><linearGradient id="paperB" x1="0" y1="0" x2="0" y2="1"><stop offset="0" stop-color="#fff"/><stop offset="1" stop-color="#dadada"/></linearGradient></defs>
    <path d="M0,382 C120,430 240,458 360,455 C480,452 600,420 702,368 L702,496 L0,496Z" fill="url(#paperB)"/>
    <path d="M0,390 C120,438 240,466 360,463 C480,460 600,428 702,376" fill="none" stroke="#1f6fd1" stroke-width="6"/>
    <path d="M0,380 C120,428 240,456 360,453 C480,450 600,418 702,366" fill="none" stroke="var(--red)" stroke-width="8"/>
  </svg>
  <div class="fold" style="left:234px"></div><div class="fold" style="left:468px"></div>

  <div class="content services">
    <h2>Our Services</h2>
    <div class="svc"><svg width="11" height="11" viewBox="0 0 11 11"><circle cx="5.5" cy="5.5" r="4.8" fill="none" stroke="#fff"/><path d="M3.3 5.6l1.6 1.6 3-3.2" fill="none" stroke="#fff" stroke-width="1.1"/></svg><div><b>First Class Patient Care -</b>We always put patient needs and safety first.</div></div>
    <div class="svc"><svg width="11" height="11" viewBox="0 0 11 11"><circle cx="5.5" cy="5.5" r="4.8" fill="none" stroke="#fff"/><path d="M3.3 5.6l1.6 1.6 3-3.2" fill="none" stroke="#fff" stroke-width="1.1"/></svg><div><b>High End Technology –</b>We are always current on the latest socket and component technology</div></div>
    <div class="svc"><svg width="11" height="11" viewBox="0 0 11 11"><circle cx="5.5" cy="5.5" r="4.8" fill="none" stroke="#fff"/><path d="M3.3 5.6l1.6 1.6 3-3.2" fill="none" stroke="#fff" stroke-width="1.1"/></svg><div><b>Experience -</b>15 years technical &amp; practitioner experience</div></div>
    <div class="svc"><svg width="11" height="11" viewBox="0 0 11 11"><circle cx="5.5" cy="5.5" r="4.8" fill="none" stroke="#fff"/><path d="M3.3 5.6l1.6 1.6 3-3.2" fill="none" stroke="#fff" stroke-width="1.1"/></svg><div><b>Fast Turnaround –</b>Same day prosthetic service available</div></div>
    <div class="svc"><svg width="11" height="11" viewBox="0 0 11 11"><circle cx="5.5" cy="5.5" r="4.8" fill="none" stroke="#fff"/><path d="M3.3 5.6l1.6 1.6 3-3.2" fill="none" stroke="#fff" stroke-width="1.1"/></svg><div><b>Firm Belief In Teamwork –</b>We love to work with the patient, rehabilitative staff and physicians to achieve the patient’s goal.</div></div>
  </div>

  <div class="content includes">
    <h3>Prosthetic Services Include but are not limited to:</h3>
    <p>AK Prosthesis (Transfemoral), BK Prosthesis (Transtibial), AE Prosthesis (Transhumeral), BE Prosthesis (Transradial), Partial Foot Prosthesis, Hip Disarticulation Prosthesis, Shoulder Disarticulation Prosthesis, Micro-Processor Knees, Myo-electric Components, and anything you can think of related to the absence of a limb.</p>
  </div>

  <div class="content benefits">
    <h3>All of these combined allow us to provide the best possible patient outcome</h3>
    <ul>
      <li><svg width="10" height="10" viewBox="0 0 11 11"><circle cx="5.5" cy="5.5" r="4.8" fill="none" stroke="var(--red)"/><path d="M3.3 5.6l1.6 1.6 3-3.2" fill="none" stroke="var(--red)" stroke-width="1.1"/></svg>Free consultations.</li>
      <li><svg width="10" height="10" viewBox="0 0 11 11"><circle cx="5.5" cy="5.5" r="4.8" fill="none" stroke="var(--red)"/><path d="M3.3 5.6l1.6 1.6 3-3.2" fill="none" stroke="var(--red)" stroke-width="1.1"/></svg>Same Day Prosthetic Fitting Available</li>
      <li><svg width="10" height="10" viewBox="0 0 11 11"><circle cx="5.5" cy="5.5" r="4.8" fill="none" stroke="var(--red)"/><path d="M3.3 5.6l1.6 1.6 3-3.2" fill="none" stroke="var(--red)" stroke-width="1.1"/></svg>Most items covered by Insurance</li>
      <li><svg width="10" height="10" viewBox="0 0 11 11"><circle cx="5.5" cy="5.5" r="4.8" fill="none" stroke="var(--red)"/><path d="M3.3 5.6l1.6 1.6 3-3.2" fill="none" stroke="var(--red)" stroke-width="1.1"/></svg>We accept Medicare, Medicaid, and most private insurances.</li>
    </ul>
  </div>

  <div class="content contact">
    <div><svg width="10" height="10" viewBox="0 0 8 8"><circle cx="4" cy="4" r="3.5" fill="none" stroke="var(--red)" stroke-width=".8"/><path d="M2.7 2.4l1 1-.5.6.8.8.6-.5 1 1-.6.6c-1.4-.3-2.6-1.5-2.9-2.9z" fill="var(--red)"/></svg>(901) 555-0100</div>
    <div><svg width="10" height="8" viewBox="0 0 10 8"><rect x=".5" y=".5" width="9" height="7" fill="none" stroke="var(--red)"/><path d="M.5 .5L5 4.5 9.5 .5" fill="none" stroke="var(--red)"/></svg>info@limbwell9.example</div>
  </div>
  <div class="web" style="left:517px;top:467px;font-size:11.5px"><svg width="10" height="10" viewBox="0 0 10 10"><circle cx="5" cy="5" r="4.3" fill="none" stroke="var(--red)"/><path d="M.7 5h8.6M5 .7c-2.4 2.6-2.4 6 0 8.6M5 .7c2.4 2.6 2.4 6 0 8.6" fill="none" stroke="var(--red)" stroke-width=".7"/></svg>www.limbwell9.example</div>
</section>

</body>
</html>
```